Podiatry clinic requires a modern revamp and editing of existing website.

I would like a fresh new look and updated information for my current business website. An easy to navigate site with prominent address and phone number for call to action. We are a podiatry clinic that focuses on general and sports podiatry.
I would like 4 pages; including Home page, About Us, Services & Contact.
www.brambleridgepodiatry.net

Target Market(s)

Active working professionals.

Industry/Entity Type

Medical

Coding

Coded - Design and coding required

Number of Pages Required

4 page

Font styles to use
Sans Serif

Colors
6b449b

Requirements
Must have
• A modern look with logo and active images; clean and uncluttered. Visible phone number and address for call to action.
• 4 pages - Home, About Us, Services, Contact.
• Home page - update address & service logos.
• About Us - update of personal information.
• Services - Revamp of existing page.
• Contact page to include Google map, email & phone number.
Nice to have
• Ability to add content easily; eg. a blog or adding video onto Home page.
• Link to Facebook page.

```html
<!DOCTYPE html>
<html lang="en">
<head>
<meta charset="utf-8">
<title>Brambleridge Podiatry – Home</title>
<link href="https://fonts.googleapis.com/css2?family=Lato:wght@400;700&family=Poppins:wght@300;400;600&display=swap" rel="stylesheet">
<style>
:root{
  --purple:#4b3596;
  --purple-footer:#5b45a3;
  --purple-text:#3e2c8c;
  --orange:#f0702a;
  --green:#7cc132;
  --ink:#333;
  --grey-bg:#ececec;
  --line:#cfcfcf;
}
*{margin:0;padding:0;box-sizing:border-box}
html,body{width:892px;height:1200px;overflow:hidden}
body{position:relative;font-family:"Lato",sans-serif;color:var(--ink);background:#fff}
.abs{position:absolute}

/* top bar */
.topbar{left:0;top:0;width:892px;height:22px;background:var(--purple)}
.social{top:7px;width:8px;height:8px;border-radius:50%;background:#fff}
.contact-chip{top:0;width:22px;height:22px;background:var(--green);display:flex;align-items:center;justify-content:center}
.topbar-text{top:0;line-height:22px;font-size:10.5px;color:#fff}

/* header */
.brand{left:74px;top:40px;display:flex;align-items:center;gap:8px}
.brand-dot{width:22px;height:22px;border-radius:50%;background:var(--purple)}
.brand-name{font-family:"Poppins",sans-serif;font-weight:600;font-size:17px;line-height:19px;color:var(--purple)}
.nav-link{top:46px;height:31px;line-height:31px;font-size:10.5px;color:var(--purple-text)}
.nav-link.active{left:373px;width:63px;text-align:center;border:1px solid var(--purple);font-weight:700}
.book-btn{left:670px;top:46px;width:149px;height:31px;background:var(--green);color:#fff;font-family:"Poppins",sans-serif;font-weight:600;font-size:11.5px;display:flex;align-items:center;justify-content:center;gap:7px}

/* hero */
.hero{left:0;top:101px;width:892px;height:350px;background:linear-gradient(160deg,#8fa3ad 0%,#6f7a80 35%,#4a4c50 65%,#2c2d30 100%)}
.hero-arrow{top:266px;width:20px;height:20px;border:1px solid #fff;display:flex;align-items:center;justify-content:center}
.hero-caption{left:0;top:409px;width:892px;text-align:center;font-family:"Poppins",sans-serif;font-weight:600;font-size:21px;color:#fff}

/* welcome */
.welcome-title{left:81px;top:476px;font-family:"Poppins",sans-serif;font-size:27px;color:var(--orange);font-weight:300;white-space:nowrap}
.welcome-title strong{color:var(--purple-text);font-weight:600}
.rule{height:1px;background:var(--line)}
.welcome-copy{left:81px;top:533px;width:520px;font-size:10px;line-height:16.5px}
.welcome-copy p{margin-bottom:8px}
.welcome-copy b{font-size:12px}
.faint-brand{left:620px;top:540px;display:flex;align-items:center;gap:10px;opacity:.25}
.faint-brand .brand-dot{width:40px;height:40px}
.faint-brand .brand-name{font-size:26px;line-height:30px}

/* services */
.services{left:0;top:689px;width:892px;height:296px;background:linear-gradient(180deg,#e6e6e6,#f1f1f1 60%,#e9e9e9)}
.section-title{left:0;top:712px;width:892px;text-align:center;font-family:"Poppins",sans-serif;font-weight:300;font-size:26px;color:var(--orange)}
.section-title strong{color:var(--purple-text);font-weight:600}
.group-title{top:776px;font-family:"Poppins",sans-serif;font-weight:600;font-size:15px;color:var(--orange);text-decoration:underline}
.treatment{font-size:11.5px;color:var(--orange);display:flex;align-items:center;gap:9px;white-space:nowrap}
.treatment svg{flex:none}
.divider{left:445px;top:782px;width:1px;height:126px;background:#c9c9c9}
.read-more{left:409px;top:932px;width:74px;height:24px;background:var(--green);color:#fff;font-size:10px;font-weight:700;display:flex;align-items:center;justify-content:center}

/* footer */
.footer{left:0;top:985px;width:892px;height:186px;background:var(--purple-footer);color:#fff}
.footer-heading{top:1012px;font-family:"Poppins",sans-serif;font-weight:600;font-size:11.5px}
.footer-heading::after{content:"";display:block;height:1px;background:rgba(255,255,255,.25);margin-top:5px}
.footer-sep{top:1030px;width:1px;height:115px;background:rgba(255,255,255,.15)}
.quick-link{left:74px;width:90px;font-size:9px;display:flex;align-items:center;gap:6px;padding-bottom:8px;border-bottom:1px solid rgba(255,255,255,.15)}
.quick-link::before{content:"";border-left:4px solid #fff;border-top:3px solid transparent;border-bottom:3px solid transparent}
.hours{left:241px;width:125px;font-size:9px;line-height:13px;padding-bottom:4px;border-bottom:1px solid rgba(255,255,255,.15)}
.hours b{font-weight:700}
.contact-row{left:444px;width:128px;font-size:8.5px;line-height:13px;display:flex;gap:7px;padding-bottom:8px;border-bottom:1px solid rgba(255,255,255,.15)}
.contact-row svg{flex:none;margin-top:2px}
.map{left:650px;top:1046px;width:169px;height:95px;background:linear-gradient(135deg,#e6e1d3,#d4cdb8 50%,#c9d2d8);border:2px solid #fff}
.copyright{left:0;top:1171px;width:892px;height:29px;background:var(--green);text-align:center;line-height:29px;font-size:10px;color:#333}
.copyright b{color:#222}
</style>
</head>
<body>

<!-- top bar -->
<div class="abs topbar"></div>
<span class="abs social" style="left:428px"></span>
<span class="abs social" style="left:454px"></span>
<span class="abs social" style="left:482px"></span>
<span class="abs social" style="left:510px"></span>
<div class="abs contact-chip" style="left:535px">
  <svg width="10" height="10" viewBox="0 0 24 24"><path fill="#fff" d="M6.6 10.8a15 15 0 0 0 6.6 6.6l2.2-2.2c.3-.3.7-.4 1-.2 1.1.4 2.3.6 3.6.6.6 0 1 .4 1 1V20c0 .6-.4 1-1 1A17 17 0 0 1 3 4c0-.6.4-1 1-1h3.5c.6 0 1 .4 1 1 0 1.3.2 2.5.6 3.6.1.3 0 .7-.2 1z"/></svg>
</div>
<span class="abs topbar-text" style="left:564px">832-555-0194</span>
<div class="abs contact-chip" style="left:647px">
  <svg width="11" height="9" viewBox="0 0 22 16"><path fill="#fff" d="M0 0h22v16H0z"/><path d="M0 0l11 8 11-8" fill="none" stroke="#7cc132" stroke-width="2"/></svg>
</div>
<span class="abs topbar-text" style="left:675px">hello@brambleridgepodiatry.net</span>

<!-- header -->
<div class="abs brand"><span class="brand-dot"></span><span class="brand-name">Brambleridge<br>Podiatry</span></div>
<a class="abs nav-link active">Home</a>
<a class="abs nav-link" style="left:452px">About Us</a>
<a class="abs nav-link" style="left:528px">Services</a>
<a class="abs nav-link" style="left:601px">Contact</a>
<a class="abs book-btn">
  <svg width="14" height="14" viewBox="0 0 24 24"><circle cx="9" cy="6" r="4" fill="#fff"/><path d="M2 22c0-6 3-9 7-9s7 3 7 9z" fill="#fff"/></svg>
  Book Appointment
</a>

<!-- hero -->
<div class="abs hero" role="img" aria-label="Photo of a runner's shoes on a treadmill with highlighted ankle bones"></div>
<div class="abs hero-arrow" style="left:44px"><svg width="10" height="8" viewBox="0 0 10 8"><path d="M10 4H2M4 1L1 4l3 3" fill="none" stroke="#fff" stroke-width="1.5"/></svg></div>
<div class="abs hero-arrow" style="left:827px"><svg width="10" height="8" viewBox="0 0 10 8"><path d="M0 4h8M6 1l3 3-3 3" fill="none" stroke="#fff" stroke-width="1.5"/></svg></div>
<div class="abs hero-caption">Brambleridge Podiatry is a Podiatry clinic in the heart of Melbourne</div>

<!-- welcome -->
<h1 class="abs welcome-title">Welcome to <strong>Brambleridge Podiatry</strong></h1>
<div class="abs rule" style="left:81px;top:521px;width:479px"></div>
<div class="abs welcome-copy">
  <p>Brambleridge Podiatry is a Podiatry clinic in the heart of Melbourne CBD. We are located between Bramble &amp; Ridge Streets in the Ridgeview Business Centre / Linden House Complex. Our podiatrists are fully qualified health professionals who are able to diagnose, treat, manage or help to prevent all medical conditions that affect the feet and lower limb.</p>
  <p>We provide General Podiatry Treatment and some Specialised Services in relation to various foot conditions, including Sports Injuries, Orthotic Therapy and Nail Surgery.</p>
  <p>For Appointments or Enquiries please call us on <b>1300 482 207</b> or email: <b>info@brambleridgepodiatry.net</b></p>
</div>
<div class="abs faint-brand"><span class="brand-dot"></span><span class="brand-name">Brambleridge<br>Podiatry</span></div>

<!-- services -->
<div class="abs services" role="img" aria-label="Faded photo of a running shoe in motion"></div>
<h2 class="abs section-title">Our <strong>Services</strong></h2>
<div class="abs rule" style="left:340px;top:758px;width:211px"></div>

<span class="abs group-title" style="left:83px">General Treatments</span>
<div class="abs divider"></div>
<span class="abs group-title" style="left:510px">Specialised Treatments</span>

<svg width="0" height="0" style="position:absolute">
  <defs>
    <symbol id="tick" viewBox="0 0 14 14"><rect x="1" y="2" width="11" height="11" fill="none" stroke="#f0702a" stroke-width="1.2"/><path d="M3.5 7l3 3L13 1.5" fill="none" stroke="#f0702a" stroke-width="1.5"/></symbol>
  </defs>
</svg>

<div class="abs treatment" style="left:85px;top:819px"><svg width="14" height="14"><use href="#tick"/></svg>Nails</div>
<div class="abs treatment" style="left:187px;top:819px"><svg width="14" height="14"><use href="#tick"/></svg>Corns</div>
<div class="abs treatment" style="left:313px;top:819px"><svg width="14" height="14"><use href="#tick"/></svg>Callus</div>
<div class="abs treatment" style="left:85px;top:854px"><svg width="14" height="14"><use href="#tick"/></svg>Warts</div>
<div class="abs treatment" style="left:187px;top:854px"><svg width="14" height="14"><use href="#tick"/></svg>Skin Disorders</div>
<div class="abs treatment" style="left:313px;top:854px"><svg width="14" height="14"><use href="#tick"/></svg>Heel Pain</div>
<div class="abs treatment" style="left:85px;top:889px"><svg width="14" height="14"><use href="#tick"/></svg>Knee Pain</div>
<div class="abs treatment" style="left:187px;top:889px"><svg width="14" height="14"><use href="#tick"/></svg>Toe Deformities</div>

<div class="abs treatment" style="left:511px;top:819px"><svg width="14" height="14"><use href="#tick"/></svg>Diabetic Management</div>
<div class="abs treatment" style="left:700px;top:819px"><svg width="14" height="14"><use href="#tick"/></svg>Nail Surgery</div>
<div class="abs treatment" style="left:511px;top:853px"><svg width="14" height="14"><use href="#tick"/></svg>Gait Analysis</div>
<div class="abs treatment" style="left:700px;top:853px"><svg width="14" height="14"><use href="#tick"/></svg>Orthotic Therapy</div>
<div class="abs treatment" style="left:511px;top:889px"><svg width="14" height="14"><use href="#tick"/></svg>Biomechanical Assessment</div>

<a class="abs read-more">Read More</a>

<!-- footer -->
<div class="abs footer"></div>
<div class="abs footer-heading" style="left:74px;width:90px;color:#fff">Quick Links</div>
<div class="abs footer-heading" style="left:241px;width:128px;color:#fff">Hours of Operation</div>
<div class="abs footer-heading" style="left:444px;width:139px;color:#fff">Contact Details</div>
<div class="abs footer-heading" style="left:650px;width:169px;color:#fff">Location Map</div>

<div class="abs footer-sep" style="left:202px"></div>
<div class="abs footer-sep" style="left:408px"></div>
<div class="abs footer-sep" style="left:616px"></div>

<div class="abs quick-link" style="top:1044px;color:#fff">Home</div>
<div class="abs quick-link" style="top:1073px;color:#fff">About Us</div>
<div class="abs quick-link" style="top:1104px;color:#fff">Services</div>
<div class="abs quick-link" style="top:1135px;color:#fff;border-bottom:0">Contact</div>

<div class="abs hours" style="top:1044px;color:#fff"><b>Monday to Thursday</b><br>10:00 am to 07:00 pm</div>
<div class="abs hours" style="top:1084px;color:#fff"><b>Friday &amp; Satuday</b><br>10:00 am to 05:00 pm</div>
<div class="abs hours" style="top:1122px;color:#fff;border-bottom:0"><b>Sunday</b><br>10:00 am to 01:00 pm</div>

<div class="abs contact-row" style="top:1043px;color:#fff">
  <svg width="7" height="10" viewBox="0 0 14 20"><path fill="#fff" d="M7 0a7 7 0 0 0-7 7c0 5 7 13 7 13s7-8 7-13a7 7 0 0 0-7-7zm0 10a3 3 0 1 1 0-6 3 3 0 0 1 0 6z"/></svg>
  <span>Suite 214 / 96 Bramble Lane<br>Melbourne 3000</span>
</div>
<div class="abs contact-row" style="top:1094px;color:#fff">
  <svg width="8" height="8" viewBox="0 0 24 24"><path fill="#fff" d="M6.6 10.8a15 15 0 0 0 6.6 6.6l2.2-2.2c.3-.3.7-.4 1-.2 1.1.4 2.3.6 3.6.6.6 0 1 .4 1 1V20c0 .6-.4 1-1 1A17 17 0 0 1 3 4c0-.6.4-1 1-1h3.5c.6 0 1 .4 1 1 0 1.3.2 2.5.6 3.6.1.3 0 .7-.2 1z"/></svg>
  <span>1300 482 207</span>
</div>
<div class="abs contact-row" style="top:1132px;color:#fff;border-bottom:0">
  <svg width="8" height="7" viewBox="0 0 22 16"><path fill="#fff" d="M0 0h22v16H0z"/><path d="M0 0l11 8 11-8" fill="none" stroke="#5b45a3" stroke-width="2"/></svg>
  <span>info@brambleridgepodiatry.net</span>
</div>

<div class="abs map" role="img" aria-label="Street map showing the clinic location in Melbourne CBD"></div>

<div class="abs copyright">Copyright © 2016 <b>Brambleridge Podiatry</b>. All Rights Reserved.</div>

</body>
</html>
```